Homepage for the brisk-find Web Application

At the end of this text, you will find a link to a website that is under construction for a webApp that I intend to launch soon. The contest goal is for you to make redesign the homepage in a nice, fresh, modern Style. Only design, no coding necessary. It needs to have a responsive version for small screens like smart phones. Attached is the text for it, and some images that you may use. You are welcome to find or create additional supporting images. You can use PixTrove.example or similar service to find new images as long as I can purchase the non-exclusive use rights for the images at similar prices. The contest is just for the home page. However, the winner, if I like the work and we can agree on a fair price, could be contracted on a one-on-one basis to do the rest of the site. You are welcome to suggest minor changes like font sizes and minor variations on the Header banner, but that banner is consistent with the user interface of the application therefore should not change too much. The information should flow somewhat continually without much use of side bars or things like that.
https://www.brisk-find.example
Sincerely,
Marco D. Ferral

```html
<!DOCTYPE html>
<html lang="en">
<head>
<meta charset="utf-8">
<title>Brisk Find — Home</title>
<link rel="stylesheet" href="https://fonts.googleapis.com/css2?family=Montserrat:ital,wght@0,300;0,400;0,500;0,600;0,700;0,800;1,300&display=swap">
<style>
:root{
  --orange:#ff7f50;
  --cyan:#4fd0d8;
  --teal-dark:#123c4f;
  --teal:#1f6a84;
  --blue:#0a5fa8;
  --blue-light:#17a5de;
  --sky:#d5efff;
  --ink:#1b1b1b;
  --grey:#8a8a8a;
  --panel:#eeeeee;
  --white:#ffffff;
}
*{box-sizing:border-box;margin:0;padding:0}
html,body{width:1200px;height:3949px;overflow:hidden}
body{font-family:"Montserrat",sans-serif;color:var(--ink);background:var(--white);position:relative}
section,header,nav,footer{position:absolute;left:0;width:1200px;overflow:hidden}
.abs{position:absolute}
.center{text-align:center;left:0;width:1200px}

/* header */
.site-header{top:0;height:127px;background:var(--white)}
.logo{left:104px;top:36px;font-size:40px;font-weight:600;color:var(--orange);display:flex;align-items:center;gap:8px}
.logo-dot{width:16px;height:16px;border-radius:50%;background:var(--cyan)}
.contact-block{top:55px;font-size:12px;color:#555}
.contact-block b{display:block;color:var(--cyan);font-weight:500;margin-bottom:2px}
.follow-row{display:flex;gap:3px;margin-top:3px}
.follow-row i{width:11px;height:11px;background:#444;display:block}

/* nav */
.main-nav{top:127px;height:40px;background:var(--orange)}
.main-nav a{position:absolute;top:0;height:40px;line-height:40px;color:var(--white);font-size:11px;font-weight:500;text-decoration:none;transform:translateX(-50%)}
.main-nav a.active{background:var(--cyan);width:92px;text-align:center}

/* hero */
.hero{top:167px;height:584px;background:linear-gradient(90deg,#0e2f44 0%,#17506a 45%,#1f6d88 100%)}
.hero-art{left:0;top:70px;width:582px;height:480px;background:radial-gradient(ellipse at 55% 45%,#3fb8e0 0%,#1a6f9a 45%,rgba(18,60,80,0) 75%)}
.hero-kicker{left:616px;top:160px;font-size:40px;font-weight:300;font-style:italic;color:var(--cyan)}
.hero-title{left:616px;top:208px;font-size:46px;font-weight:800;color:var(--white);line-height:40px}
.hero-sub{left:616px;top:290px;font-size:46px;font-weight:300;color:var(--cyan)}
.btn-fill,.btn-line{position:absolute;height:50px;border-radius:10px;font-size:20px;font-weight:400;display:flex;align-items:center;justify-content:center}
.btn-fill{background:var(--orange);color:var(--white)}
.btn-line{border:2px solid var(--white);color:var(--white)}

/* headings */
.kicker{font-size:11px;font-weight:600;color:var(--blue-light);text-transform:uppercase}
.h2{font-size:29px;font-weight:600;color:var(--ink)}
.lead{font-size:11.5px;color:#555;line-height:15px}

/* pricing */
.pricing{top:751px;height:605px;background:var(--white)}
.pricing-ghost{left:0;top:10px;width:380px;height:595px;background:linear-gradient(120deg,rgba(79,208,216,.12),rgba(255,127,80,.06) 60%,rgba(255,255,255,0))}
.plan{position:absolute;top:193px;width:197px;height:328px;background:var(--sky)}
.plan-head{height:95px;background:var(--orange);color:var(--white);text-align:center;padding-top:14px}
.plan-head .price{font-size:38px;font-weight:700;line-height:40px}
.plan-head .name{font-size:18px;font-weight:600}
.plan ul{list-style:none;padding:28px 0 0 32px}
.plan li{font-size:11px;color:#777;height:30.5px;display:flex;gap:10px}
.plan li svg{flex:none;margin-top:1px}
.btn-blue{position:absolute;left:35px;top:264px;width:116px;height:35px;border-radius:18px;background:var(--blue);color:var(--white);font-size:11.5px;font-weight:600;display:flex;align-items:center;justify-content:center}

/* welcome */
.welcome{top:1356px;height:384px;background:var(--panel)}
.welcome-photo{left:132px;top:95px;width:314px;height:204px;background:linear-gradient(135deg,#c7ccd0,#6e747a 55%,#2e3236)}
.btn-pill{position:absolute;border-radius:20px;background:var(--orange);color:var(--white);font-size:9.5px;font-weight:700;letter-spacing:.5px;display:flex;align-items:center;justify-content:center}

/* blog */
.blog{top:1740px;height:654px}
.post-photo{position:absolute;top:205px;width:284px;height:188px}
.post-meta{position:absolute;top:418px;font-size:9px;color:#333}
.post-title{position:absolute;top:446px;width:240px;font-size:15px;font-weight:600;color:var(--orange);line-height:19px}
.post-text{position:absolute;top:496px;width:250px;font-size:9px;color:#888;line-height:13px}

/* download */
.download{top:2394px;height:334px;background:linear-gradient(90deg,#0a4f9c 0%,#0d6cb8 55%,#16a3dc 100%)}
.download .h2{color:var(--white);font-size:30px}
.store{position:absolute;top:222px;height:45px;border:2px solid var(--white);border-radius:10px;color:var(--white);font-size:11px;font-weight:600;display:flex;align-items:center;justify-content:center;gap:8px}
.store i{width:14px;height:14px;border-radius:50%;background:var(--white);display:block}

/* reviews */
.reviews{top:2728px;height:518px}
.avatar{left:554px;top:183px;width:70px;height:70px;border-radius:50%;background:radial-gradient(circle,#4f5e6e,#0f1b2a)}
.reviewer{font-size:25px;font-weight:600;color:var(--blue-light)}
.quote{font-size:11.5px;font-style:italic;color:#444;line-height:15px}
.dots{display:flex;gap:10px;justify-content:center}
.dots i{width:6px;height:6px;border-radius:50%;background:#ccc;display:block}
.dots i:first-child{background:#888}

/* contact */
.contact{top:3246px;height:578px}
.contact-art{left:153px;top:72px;width:429px;height:444px;background:linear-gradient(140deg,#bdeef2 0%,#4fd0d8 45%,#1a9bb4 100%);clip-path:polygon(20% 0,100% 15%,100% 80%,40% 100%,0 75%,0 20%)}
.field{position:absolute;left:644px;width:334px;height:34px;border:1px solid #e2e2e2;font-size:11px;color:#888;padding:10px 18px}
.field span{color:var(--orange)}

/* footer */
.site-footer{top:3824px;height:125px;background:linear-gradient(90deg,#0a4f9c,#16a3dc)}
.copy{left:109px;top:58px;font-size:12px;color:var(--white)}
.social{position:absolute;top:46px;width:36px;height:36px;border:1.5px solid var(--white);border-radius:50%}
</style>
</head>
<body>

<header class="site-header">
  <div class="abs logo"><span class="logo-dot"></span>Brisk Find</div>
  <div class="abs contact-block" style="left:535px"><b>&#9742; Call Us Now</b>+91 0800 555 010 2233</div>
  <div class="abs contact-block" style="left:783px"><b>&#9993; Contact Email</b>info@brisk-find.example</div>
  <div class="abs contact-block" style="left:1019px"><b>Follow Us</b><div class="follow-row"><i></i><i></i><i></i><i></i><i></i></div></div>
</header>

<nav class="main-nav">
  <a class="active" href="#" style="left:152px">HOME</a>
  <a href="#" style="left:299px">ABOUT US</a>
  <a href="#" style="left:435px">PRICING</a>
  <a href="#" style="left:553px">BLOG</a>
  <a href="#" style="left:651px">FAQS</a>
  <a href="#" style="left:772px">SUPPORT</a>
  <a href="#" style="left:897px">REVIEWS</a>
  <a href="#" style="left:1054px">CONTACT US</a>
</nav>

<section class="hero">
  <div class="abs hero-art" role="img" aria-label="Hand touching a glowing transparent tablet showing document folders"></div>
  <div class="abs hero-kicker">Keeping track of all your</div>
  <div class="abs hero-title">PAPER DOCUMENTS<br>&amp; OTHER BELONGINGS</div>
  <div class="abs hero-sub">has never been easier!</div>
  <div class="btn-fill" style="left:616px;top:382px;width:176px">Free Trial</div>
  <div class="btn-line" style="left:820px;top:382px;width:207px">Download App</div>
</section>

<section class="pricing">
  <div class="abs pricing-ghost" role="img" aria-label="Faint illustration of a phone and a person with a filing drawer"></div>
  <div class="abs center kicker" style="top:61px">Get started now</div>
  <div class="abs center h2" style="top:78px">Our Pricing Plans</div>
  <div class="abs center lead" style="top:122px">Lorem ipsum dolor sit amet, consectetur adipiscing elit. Quid autem<br>habent admirationis, cum prope accesseris</div>

  <div class="plan" style="left:172px">
    <div class="plan-head"><div class="price">$125</div><div class="name">STANDARD</div></div>
    <ul>
      <li><svg width="10" height="9"><path d="M1 5l3 3 5-7" stroke="#ff7f50" stroke-width="2" fill="none"/></svg>Dolor sit amet</li>
      <li><svg width="10" height="9"><path d="M1 5l3 3 5-7" stroke="#ff7f50" stroke-width="2" fill="none"/></svg>Nam quibus rebus</li>
      <li><svg width="10" height="9"><path d="M1 5l3 3 5-7" stroke="#ff7f50" stroke-width="2" fill="none"/></svg>Collatio igitur ista</li>
      <li><svg width="10" height="9"><path d="M1 5l3 3 5-7" stroke="#ff7f50" stroke-width="2" fill="none"/></svg>Hoc non est</li>
    </ul>
    <div class="btn-blue">Purchase</div>
  </div>
  <div class="plan" style="left:391px">
    <div class="plan-head"><div class="price">$256</div><div class="name">BRONZE</div></div>
    <ul>
      <li><svg width="10" height="9"><path d="M1 5l3 3 5-7" stroke="#ff7f50" stroke-width="2" fill="none"/></svg>Dolor sit amet</li>
      <li><svg width="10" height="9"><path d="M1 5l3 3 5-7" stroke="#ff7f50" stroke-width="2" fill="none"/></svg>Nam quibus rebus</li>
      <li><svg width="10" height="9"><path d="M1 5l3 3 5-7" stroke="#ff7f50" stroke-width="2" fill="none"/></svg>Collatio igitur ista</li>
      <li><svg width="10" height="9"><path d="M1 5l3 3 5-7" stroke="#ff7f50" stroke-width="2" fill="none"/></svg>Hoc non est</li>
    </ul>
    <div class="btn-blue">Purchase</div>
  </div>
  <div class="plan" style="left:612px">
    <div class="plan-head"><div class="price">$645</div><div class="name">GOLD</div></div>
    <ul>
      <li><svg width="10" height="9"><path d="M1 5l3 3 5-7" stroke="#ff7f50" stroke-width="2" fill="none"/></svg>Dolor sit amet</li>
      <li><svg width="10" height="9"><path d="M1 5l3 3 5-7" stroke="#ff7f50" stroke-width="2" fill="none"/></svg>Nam quibus rebus</li>
      <li><svg width="10" height="9"><path d="M1 5l3 3 5-7" stroke="#ff7f50" stroke-width="2" fill="none"/></svg>Collatio igitur ista</li>
      <li><svg width="10" height="9"><path d="M1 5l3 3 5-7" stroke="#ff7f50" stroke-width="2" fill="none"/></svg>Hoc non est</li>
    </ul>
    <div class="btn-blue">Purchase</div>
  </div>
  <div class="plan" style="left:831px">
    <div class="plan-head"><div class="price">$895</div><div class="name">COMPLETE</div></div>
    <ul>
      <li><svg width="10" height="9"><path d="M1 5l3 3 5-7" stroke="#ff7f50" stroke-width="2" fill="none"/></svg>Dolor sit amet</li>
      <li><svg width="10" height="9"><path d="M1 5l3 3 5-7" stroke="#ff7f50" stroke-width="2" fill="none"/></svg>Nam quibus rebus</li>
      <li><svg width="10" height="9"><path d="M1 5l3 3 5-7" stroke="#ff7f50" stroke-width="2" fill="none"/></svg>Collatio igitur ista</li>
      <li><svg width="10" height="9"><path d="M1 5l3 3 5-7" stroke="#ff7f50" stroke-width="2" fill="none"/></svg>Hoc non est</li>
    </ul>
    <div class="btn-blue">Purchase</div>
  </div>
</section>

<section class="welcome">
  <div class="abs welcome-photo" role="img" aria-label="Hands searching through folders in an open filing cabinet drawer"></div>
  <div class="abs kicker" style="left:484px;top:100px">Find any document or item instantly!</div>
  <div class="abs h2" style="left:484px;top:118px">Welcome to Brisk Find</div>
  <p class="abs lead" style="left:484px;top:163px;width:586px;font-size:11.5px;text-align:justify">Brisk-Find is a system that allows you to quickly search for the location of every item that you store or file. It is an essential tool for keeping track of paper documents or any other kind of physical item. You'll have the ability to quickly find any item you're searching for, even years after you've stored it. More importantly, using Brisk-Find helps you save considerable space without losing speedy accessibility to your treasured items.</p>
  <div class="btn-pill" style="left:484px;top:264px;width:114px;height:35px">READ MORE</div>
</section>

<section class="blog">
  <div class="abs center kicker" style="top:70px">Ostrud an est</div>
  <div class="abs center h2" style="top:86px">Lates Blog</div>
  <div class="abs center lead" style="top:126px">Lorem ipsum dolor sit amet, cu per porro dolore nostro, partem cu per porro<br>integre corpora per ea, tation ornatus mel ad</div>

  <div class="post-photo" style="left:141px;background:linear-gradient(135deg,#e8e4e0,#b9a89a 55%,#5a3e34)" role="img" aria-label="Hand holding a smartphone beside a coffee cup"></div>
  <div class="post-meta" style="left:158px">By Admin | 4 January 2021</div>
  <div class="post-title" style="left:158px">Lorem ipsum dolor sit amet cu per porro dolore nostro</div>
  <div class="post-text" style="left:158px">Lorem ipsum dolor sit amet, cu per porro dolore nostro, partem integre corpora per ea, tation ornatus mel ad Brute voluptatibus an</div>
  <div class="btn-pill" style="left:156px;top:554px;width:114px;height:26px">READ MORE</div>

  <div class="post-photo" style="left:447px;background:linear-gradient(135deg,#2b3d4c,#6b7f8d 50%,#1a2630)" role="img" aria-label="Two colleagues looking at a computer screen"></div>
  <div class="post-meta" style="left:465px">By Admin | 4 January 2021</div>
  <div class="post-title" style="left:465px">Sum dolor sit amet cu per porro dolore nostro</div>
  <div class="post-text" style="left:465px">Lorem ipsum dolor sit amet, cu per porro dolore nostro, partem integre corpora per ea, tation ornatus mel ad Brute voluptatibus an</div>
  <div class="btn-pill" style="left:465px;top:554px;width:114px;height:26px">READ MORE</div>

  <div class="post-photo" style="left:754px;background:linear-gradient(135deg,#4a3226,#c08850 50%,#e8b84a)" role="img" aria-label="Smiling woman looking at her phone by a window"></div>
  <div class="post-meta" style="left:772px">By Admin | 4 January 2021</div>
  <div class="post-title" style="left:772px">Porro dolore nostro Lorem ipsum dolor sit ametcu per</div>
  <div class="post-text" style="left:772px">Lorem ipsum dolor sit amet, cu per porro dolore nostro, partem integre corpora per ea, tation ornatus mel ad Brute voluptatibus an</div>
  <div class="btn-pill" style="left:766px;top:550px;width:114px;height:26px">READ MORE</div>
</section>

<section class="download">
  <div class="abs center h2" style="top:58px">Download App</div>
  <p class="abs lead" style="left:230px;top:132px;width:740px;text-align:center;color:var(--white)">Lorem ipsum dolor sit amet, consectetur adipiscing elit. Quid autem habent admirationis cum prope accesseris An hoc usque c um propequaque, aliter in vita cum prope accesseris Lorem ipsum dolor sit amet, consectetur adipiscing elit. Quid autem habent um propequaque, aliter in vita cum prope accesseris Lorem ipsum dolor sit amet, consectetur adipiscing elit. Quid autem habent admirationis cum prope accesseris? An hoc usque cum propequaque, aliter in vita cum prope accesseris</p>
  <div class="store" style="left:340px;width:144px"><i></i>MOBILE SHOP</div>
  <div class="store" style="left:500px;width:159px"><i></i>DROID MARKET</div>
  <div class="store" style="left:674px;width:186px"><i></i>DESKTOP SHOP</div>
</section>

<section class="reviews">
  <div class="abs center h2" style="top:82px">Customers Reviews</div>
  <div class="abs center lead" style="top:128px">Constructio interrete. Quia nec honesto quic quam honestius nec turpi turpius.<br>Tria genera bonorum; Quid iudicant sensus?</div>
  <div class="abs avatar" role="img" aria-label="Customer portrait"></div>
  <div class="abs center reviewer" style="top:255px">Dana Wells</div>
  <div class="abs center" style="top:288px;color:var(--orange);font-size:12px;letter-spacing:2px">&#9733;&#9733;&#9733;&#9733;&#9733;</div>
  <div class="abs center quote" style="top:340px">Constructio interrete. Quia nec honesto quic quam honestius nec turpi turpius. Tria genera bonorum;<br>Quid iudicant sensus? Quae qui non vident, nihil umquam magnum ac cognitione dignum amaverunt.<br>Dicet pro me ipsa virtus nec untur. Paulum, cum regem</div>
  <div class="abs center dots" style="top:435px"><i></i><i></i><i></i><i></i><i></i><i></i><i></i></div>
  <svg class="abs" style="left:135px;top:232px" width="30" height="58"><path d="M26 2L4 29l22 27" stroke="#888" stroke-width="2" fill="none"/></svg>
  <svg class="abs" style="left:1016px;top:232px" width="30" height="58"><path d="M4 2l22 27L4 56" stroke="#888" stroke-width="2" fill="none"/></svg>
</section>

<section class="contact">
  <div class="abs contact-art" role="img" aria-label="Isometric illustration of a laptop turned into a filing cabinet with a man holding a folder"></div>
  <div class="abs h2" style="left:642px;top:78px">Get in Touch</div>
  <p class="abs lead" style="left:644px;top:120px;width:340px;font-size:11px">Lorem ipsum dolor sit amet, consectetur adipiscing elit. Quid autem habent admirationis, Non igitur de improbo, sed de callido improbo quaerimus, qualis</p>
  <div class="field" style="top:192px">Name<span>*</span></div>
  <div class="field" style="top:247px">Email<span>*</span></div>
  <div class="field" style="top:301px">Phone<span>*</span></div>
  <div class="field" style="top:356px;height:92px">Comment<span>*</span></div>
  <div class="btn-pill" style="left:642px;top:471px;width:146px;height:35px;font-size:11px">SEND MESSAGE</div>
</section>

<footer class="site-footer">
  <div class="abs copy">© 2021 Company Name All Right Reserved</div>
  <div class="social" style="left:774px"></div>
  <div class="social" style="left:827px"></div>
  <div class="social" style="left:880px"></div>
  <div class="social" style="left:932px"></div>
  <div class="social" style="left:984px"></div>
  <div class="social" style="left:1038px"></div>
</footer>

</body>
</html>
```